Birchline Septic Solutions

Would like to see some single sided ones but would also like to see some double sided with one sided only being the logo. Owners name is Colin Vandro. Phone number is 555-214-0387
Services are pumping, inspections, installs, and repairs

Contact Information for Business Card

555-241-0387 Colin Vandro Alder Falls, OH

```html
<!DOCTYPE html>
<html lang="en">
<head>
<meta charset="utf-8">
<title>Birchline Septic Solutions – Business Cards</title>
<link rel="stylesheet" href="https://fonts.googleapis.com/css2?family=Montserrat:wght@600;700&family=Roboto:wght@400;500;700&display=swap">
<style>
  :root {
    --backdrop: #e6e6e6;
    --card: #2b2b2b;
    --card-dark: #232323;
    --teal: #2bb8b3;
    --white: #ffffff;
    --soft-white: #d9d9d9;
    --rule: #8a8a8a;
    --scene-light: #4a4a4a;
    --scene-dark: #1f1f1f;
  }
  * { box-sizing: border-box; margin: 0; padding: 0; }
  html, body {
    width: 1200px; height: 802px; overflow: hidden;
    background: var(--backdrop);
    font-family: "Roboto", Arial, sans-serif;
  }
  .sheet {
    width: 1200px; height: 802px;
    display: flex; align-items: center; justify-content: center; gap: 40px;
  }
  .card {
    position: relative;
    width: 540px; height: 309px;
    background: var(--card);
    border-bottom: 4px solid var(--teal);
    box-shadow: 0 10px 24px rgba(0,0,0,0.18);
    overflow: hidden;
  }

  /* Front */
  .card-front .identity {
    position: absolute; top: 44px; left: 34px; right: 30px; height: 130px;
    display: flex; align-items: center;
  }
  .brand-mark {
    width: 210px; color: var(--white);
    font-family: "Montserrat", Arial, sans-serif; font-weight: 700;
    text-align: center; line-height: 1;
  }
  .brand-mark .brand-main { font-size: 34px; letter-spacing: 1px; display: block; }
  .brand-mark .brand-sub { font-size: 11px; letter-spacing: 4px; display: block; margin-top: 8px; }
  .divider-vertical {
    width: 1px; height: 110px; background: var(--rule); margin: 0 26px 0 14px;
  }
  .contact { color: var(--soft-white); font-size: 15px; line-height: 1.45; }
  .contact .person-name {
    color: var(--teal); font-weight: 700; font-size: 24px; letter-spacing: 0.5px;
    text-transform: uppercase; margin-bottom: 2px;
  }
  .contact .phone {
    color: var(--white); font-weight: 700; font-size: 17px;
    display: flex; align-items: center; gap: 6px; margin-top: 2px;
  }
  .contact .phone svg { width: 14px; height: 14px; }

  .services {
    position: absolute; left: 34px; right: 34px; top: 198px;
  }
  .services .rule {
    position: relative; height: 1px; background: var(--rule);
  }
  .services .tag {
    position: absolute; left: 50%; top: -12px; transform: translateX(-50%);
    background: var(--teal); color: var(--white);
    font-weight: 500; font-size: 14px; letter-spacing: 1px;
    padding: 4px 14px;
  }
  .services .list {
    display: flex; justify-content: center; align-items: center; gap: 12px;
    color: var(--soft-white); font-size: 15px; letter-spacing: 0.8px;
    text-transform: uppercase; padding: 24px 0 22px;
  }
  .services .dot {
    width: 7px; height: 7px; border-radius: 50%; background: var(--teal);
  }

  /* Back */
  .card-back .brand-mark-large {
    position: absolute; top: 40px; left: 0; right: 0;
    text-align: center; color: var(--white);
    font-family: "Montserrat", Arial, sans-serif; font-weight: 700; line-height: 1;
    z-index: 2;
  }
  .brand-mark-large .brand-main { font-size: 62px; letter-spacing: 3px; display: block; }
  .brand-mark-large .brand-sub { font-size: 20px; letter-spacing: 9px; display: block; margin-top: 14px; }
  .card-back .scenery {
    position: absolute; left: 0; right: 0; bottom: 0; height: 150px;
    background: linear-gradient(180deg, var(--card) 0%, var(--scene-light) 55%, var(--scene-dark) 100%);
  }
</style>
</head>
<body>
  <main class="sheet">
    <section class="card card-front" aria-label="Business card front">
      <div class="identity">
        <div class="brand-mark">
          <span class="brand-main">BIRCHLINE</span>
          <span class="brand-sub">SEPTIC SOLUTIONS</span>
        </div>
        <div class="divider-vertical"></div>
        <div class="contact">
          <p class="person-name">Colin Vandro</p>
          <p>Owners</p>
          <p>Alder Falls, OH</p>
          <p class="phone">
            <svg viewBox="0 0 24 24" aria-hidden="true"><path fill="#2bb8b3" d="M6.6 10.8a15.1 15.1 0 0 0 6.6 6.6l2.2-2.2a1 1 0 0 1 1-.25 11.4 11.4 0 0 0 3.6.57 1 1 0 0 1 1 1V20a1 1 0 0 1-1 1A17 17 0 0 1 3 4a1 1 0 0 1 1-1h3.5a1 1 0 0 1 1 1c0 1.25.2 2.45.57 3.6a1 1 0 0 1-.25 1z"/></svg>
            555-214-0387
          </p>
        </div>
      </div>
      <div class="services">
        <div class="rule"><span class="tag">SERVICES</span></div>
        <div class="list">
          <span class="dot"></span><span>Pumping</span>
          <span class="dot"></span><span>Inspections</span>
          <span class="dot"></span><span>Installs</span>
          <span class="dot"></span><span>Repairs</span>
        </div>
        <div class="rule"></div>
      </div>
    </section>

    <section class="card card-back" aria-label="Business card back">
      <div class="brand-mark-large">
        <span class="brand-main">BIRCHLINE</span>
        <span class="brand-sub">SEPTIC SOLUTIONS</span>
      </div>
      <div class="scenery" role="img" aria-label="Embossed mountain peak with pine forest silhouette along the bottom of the card"></div>
    </section>
  </main>
</body>
</html>
```